Non fiction leadership Book Cover design needed for “Stay Bold: Build On Lasting Discipline”

I need a front cover design for a new book 6 X 9 traditional non-fiction book.

Title: "Stay BOLD - Build On Lasting Discipline"

The subtitle is not finalized- so use 2 lines of smaller dummy text

My brand guide is attached (please use the tan color sparingly)

I'd like to see BOLD look like it is in motion and "flying" across the page

Need CREATIVE designs and options

Do not want my picture on the front cover - I do want it on the back cover.

On the front cover I’d like to see creative use of font to create movement on “BOLD”

Target Market(s)

Business leaders

Industry/Entity Type

Aviation

Font styles to use
Other font styles liked:
• See style guide- can add additional font (modern script or san serif)

Colors
0054AA
0677BA
7BADD7
CADEEF
E8F1F8
EB3D1F
EC4F4E
F09395
F8D3D4
FCEDEE

Requirements
Must have
• Creative font use, using perspective to create movement/motion on BOLD
Should not have
• My picture on the front cover- my picture should be on the back cover

```html
<!DOCTYPE html>
<html lang="en">
<head>
<meta charset="UTF-8">
<title>Stay Bold: Build On Lasting Discipline — Book Cover</title>
<link rel="stylesheet" href="https://fonts.googleapis.com/css2?family=Lobster&family=Bebas+Neue&display=swap">
<style>
  :root {
    --cover-bg: #4d4c47;
    --ink-light: #ffffff;
    --tan-top: #e6bd8e;
    --tan-mid: #c88a55;
    --tan-bottom: #8e4a15;
    --brand-navy: #0054aa;
    --brand-blue: #0677ba;
    --brand-sky: #7badd7;
    --brand-mist: #cadeef;
    --brand-red: #eb3d1f;
    --brand-coral: #ec4f4e;
    --brand-blush: #f09395;
  }
  * { margin: 0; padding: 0; box-sizing: border-box; }
  html, body {
    width: 800px;
    height: 1200px;
    overflow: hidden;
    background: var(--cover-bg);
  }
  .cover {
    position: relative;
    width: 800px;
    height: 1200px;
    background: var(--cover-bg);
    overflow: hidden;
  }
  .title {
    font-family: "Lobster", cursive;
    font-weight: 400;
  }
  .title-line {
    position: absolute;
    left: 0;
    width: 100%;
    text-align: center;
    line-height: 1;
    white-space: nowrap;
  }
  .title-stay {
    top: 10px;
    font-size: 290px;
    letter-spacing: -4px;
    background: linear-gradient(180deg, var(--tan-top) 15%, var(--tan-mid) 55%, var(--tan-bottom) 92%);
    -webkit-background-clip: text;
    background-clip: text;
    color: transparent;
  }
  .speed-lines {
    position: absolute;
    left: 70px;
    top: 355px;
    width: 260px;
    height: 120px;
  }
  .title-bold {
    top: 340px;
    left: 290px;
    width: auto;
    font-size: 128px;
    letter-spacing: 2px;
    background: linear-gradient(90deg, var(--brand-blush) 0%, var(--brand-coral) 35%, var(--brand-red) 100%);
    -webkit-background-clip: text;
    background-clip: text;
    color: transparent;
    transform-origin: left center;
    transform: perspective(520px) rotateY(-28deg) skewX(-14deg);
  }
  .title-build {
    top: 468px;
    font-size: 180px;
    color: var(--ink-light);
    letter-spacing: -2px;
  }
  .title-lasting {
    top: 728px;
    font-size: 92px;
    color: var(--ink-light);
    letter-spacing: -1px;
  }
  .subtitle {
    position: absolute;
    top: 928px;
    left: 0;
    width: 100%;
    text-align: center;
    font-family: "Bebas Neue", sans-serif;
    font-size: 46px;
    line-height: 58px;
    letter-spacing: 4px;
    color: var(--ink-light);
  }
  .author {
    position: absolute;
    top: 1096px;
    left: 0;
    width: 100%;
    text-align: center;
    font-family: "Bebas Neue", sans-serif;
    font-size: 68px;
    line-height: 1;
    letter-spacing: 6px;
    color: var(--ink-light);
  }
</style>
</head>
<body>
  <main class="cover">
    <svg class="speed-lines" viewBox="0 0 260 120" aria-hidden="true">
      <g fill="none" stroke-linecap="round">
        <line x1="70" y1="22" x2="250" y2="22" stroke="var(--brand-mist)" stroke-width="4"/>
        <line x1="10" y1="44" x2="240" y2="44" stroke="var(--brand-sky)" stroke-width="7"/>
        <line x1="40" y1="66" x2="245" y2="66" stroke="var(--brand-blue)" stroke-width="9"/>
        <line x1="0" y1="88" x2="235" y2="88" stroke="var(--brand-navy)" stroke-width="6"/>
        <line x1="90" y1="106" x2="240" y2="106" stroke="var(--brand-red)" stroke-width="3"/>
      </g>
    </svg>
    <h1 class="title">
      <span class="title-line title-stay">Stay</span>
      <span class="title-line title-bold">BOLD</span>
      <span class="title-line title-build">Build On</span>
      <span class="title-line title-lasting">Lasting Discipline</span>
    </h1>
    <p class="subtitle">Unlock your inner potential<br>and soar to new heights</p>
    <p class="author">Author Name</p>
  </main>
</body>
</html>
```